Local Roofing/Construction company business needs new biz card design

We need a new business card design, current cards are from the start of this operation and generic at best. We are a local Construction Company (General Contractor) with a majority of our work originating from insurance claims-exterior finish work is the main focus (Roofs-Siding-Gutters etc). Heavily involved with homeowners and the low ball offers they receive from insurance company's after a insurable event takes place. I have attached some of our original logo file(s) below.

```html
<!DOCTYPE html>
<html lang="en">
<head>
<meta charset="utf-8">
<title>Stonefield Construction – Business Card</title>
<link href="https://fonts.googleapis.com/css2?family=Open+Sans:wght@400;600;700&display=swap" rel="stylesheet">
<style>
  :root{
    --stage:#232323;
    --card:#061c20;
    --card-deep:#04151a;
    --green:#4dbb6a;
    --white:#f4f6f5;
    --pattern-light:#5a6466;
  }
  *{box-sizing:border-box;margin:0;padding:0}
  html,body{width:1200px;height:780px;overflow:hidden;background:var(--stage)}
  body{position:relative;font-family:"Open Sans",Arial,sans-serif;color:var(--white)}

  .card{
    position:absolute;top:231px;width:555px;height:317px;
    background:var(--card);
    border:2px solid var(--green);
    border-radius:3px;
    overflow:hidden;
  }
  .card--back{left:30px}
  .card--front{left:615px}

  /* back side */
  .monogram-pattern{
    position:absolute;inset:0;
    background:linear-gradient(205deg,var(--pattern-light) 0%,#1b2a2d 35%,var(--card-deep) 70%);
    opacity:.85;
  }
  .brand-badge{
    position:absolute;display:flex;align-items:center;gap:8px;
    background:var(--green);color:var(--white);
    font-weight:700;text-transform:uppercase;letter-spacing:.04em;
    white-space:nowrap;
    clip-path:polygon(6% 0,100% 0,100% 70%,95% 100%,0 100%,0 30%);
  }
  .brand-badge__mark{width:14px;height:14px;background:var(--card);flex:none}
  .card--back .brand-badge{right:45px;bottom:50px;padding:9px 18px;font-size:14px}

  /* front side */
  .card--front .brand-badge{left:28px;top:96px;padding:14px 24px;font-size:17px;gap:12px}
  .card--front .brand-badge__mark{width:20px;height:20px}

  .person{position:absolute;right:44px;top:24px;text-align:right;z-index:1}
  .person__name{color:var(--green);font-weight:700;font-size:26px;line-height:1.1;white-space:nowrap}
  .person__role{font-size:14px;font-weight:600;margin-top:2px}
  .accent-bar{position:absolute;right:0;top:18px;width:20px;height:54px;background:var(--green)}

  .monogram-emboss{
    position:absolute;right:20px;bottom:18px;width:250px;height:140px;
    background:linear-gradient(160deg,#9aa3a3 0%,#22383b 22%,#0b2226 55%,var(--card-deep) 100%);
    opacity:.7;border-radius:4px;
  }

  .contact{position:absolute;left:38px;bottom:24px;font-size:13.5px;line-height:1.45}
  .contact__address{margin-bottom:10px}
  .contact__list{list-style:none}
  .contact__item{display:flex;align-items:center;gap:9px;white-space:nowrap}
  .contact__icon{width:13px;height:13px;flex:none}
</style>
</head>
<body>

  <section class="card card--back" aria-label="Card back">
    <div class="monogram-pattern" role="img" aria-label="Repeating company monogram pattern fading from grey to dark"></div>
    <div class="brand-badge"><span class="brand-badge__mark"></span>Stonefield Construction</div>
  </section>

  <section class="card card--front" aria-label="Card front">
    <div class="accent-bar"></div>
    <div class="person">
      <p class="person__name">Marta Halloway</p>
      <p class="person__role">Co-Founder</p>
    </div>

    <div class="brand-badge"><span class="brand-badge__mark"></span>Stonefield Construction</div>

    <div class="monogram-emboss" role="img" aria-label="Large embossed company monogram"></div>

    <div class="contact">
      <p class="contact__address">42 Birch Hollow<br>Dr, Lakeport, MO 63011</p>
      <ul class="contact__list">
        <li class="contact__item">
          <svg class="contact__icon" viewBox="0 0 24 24"><path fill="#4dbb6a" d="M6.6 10.8a15 15 0 0 0 6.6 6.6l2.2-2.2a1 1 0 0 1 1-.25 11.4 11.4 0 0 0 3.6.57 1 1 0 0 1 1 1V20a1 1 0 0 1-1 1A17 17 0 0 1 3 4a1 1 0 0 1 1-1h3.5a1 1 0 0 1 1 1c0 1.25.2 2.450.57 3.57a1 1 0 0 1-.25 1z"/></svg>
          555-214-0190
        </li>
        <li class="contact__item">
          <svg class="contact__icon" viewBox="0 0 24 24"><path fill="#4dbb6a" d="M6.6 10.8a15 15 0 0 0 6.6 6.6l2.2-2.2a1 1 0 0 1 1-.25 11.4 11.4 0 0 0 3.6.57 1 1 0 0 1 1 1V20a1 1 0 0 1-1 1A17 17 0 0 1 3 4a1 1 0 0 1 1-1h3.5a1 1 0 0 1 1 1c0 1.25.2 2.45.57 3.57a1 1 0 0 1-.25 1z"/></svg>
          555-214-0275 (Emergency)
        </li>
        <li class="contact__item">
          <svg class="contact__icon" viewBox="0 0 24 24"><circle cx="12" cy="12" r="10" fill="none" stroke="#4dbb6a" stroke-width="2"/><path d="M2 12h20M12 2c3 3 3 17 0 20M12 2c-3 3-3 17 0 20" fill="none" stroke="#4dbb6a" stroke-width="2"/></svg>
          www.stonefieldbuild.com
        </li>
        <li class="contact__item">
          <svg class="contact__icon" viewBox="0 0 24 24"><rect x="2" y="5" width="20" height="14" rx="1" fill="none" stroke="#4dbb6a" stroke-width="2"/><path d="M2 6l10 7 10-7" fill="none" stroke="#4dbb6a" stroke-width="2"/></svg>
          hello@stonefieldbuild.com
        </li>
      </ul>
    </div>
  </section>

</body>
</html>
```